Website for IT consulting Company

I need a website upgrade, the existing site content is ok, I would also like to add a testimonial page, the site should be something that is easy for us to update content. You use the content from www.kelvanbrook.com as an example. I will also post update logo and artwork. I also need a contact form with some type of validation or captcha.

I added Coded to the Project

Please omit Address maps

Target Market(s)

small business, service oriented companies. We provide IT Consulting, support and mangement

Industry/Entity Type

Information Technology

Coding

Number of Pages Required

1 page

Font styles to use
Serif
Sans Serif

Requirements
Must have
• Contain logo attached, and content from existing web site www.kelvanbrook.com.
• Also need to update content easily, and be movable to different platforms.
• There is a catch phrase
• "Let us worry about your technology…” “ so you don’t have to!”
• Should be included.
Nice to have
• Testimonial page, Project page where we can post new and past projects and pictures
Should not have
• none

```html
<!DOCTYPE html>
<html lang="en">
<head>
<meta charset="utf-8">
<title>Kelvanbrook Technology Group</title>
<link href="https://fonts.googleapis.com/css2?family=Ubuntu:wght@400;500;700&family=Play:wght@400;700&family=Roboto:wght@300;400;500&display=swap" rel="stylesheet">
<style>
:root{
  --blue:#1b7bc3;
  --blue-dark:#1568a8;
  --ink:#1f1f1f;
  --text:#555a60;
  --muted:#8a8f95;
  --line:#cfd3d7;
  --white:#ffffff;
  --footer-bg:#eeefef;
  --black:#141414;
}
*{margin:0;padding:0;box-sizing:border-box}
html,body{width:1200px;height:2514px;overflow:hidden}
body{position:relative;background:var(--white);font-family:"Roboto",Arial,sans-serif;color:var(--text)}
h1,h2{font-weight:400}

/* header */
.site-header{position:absolute;left:0;top:0;width:1200px;height:106px;background:var(--white)}
.brand{position:absolute;left:77px;top:18px;display:flex;align-items:center;gap:12px}
.brand-square{width:30px;height:30px;background:var(--blue)}
.brand-name{font-family:"Ubuntu",sans-serif;font-weight:700;font-size:38px;color:var(--blue);letter-spacing:1px;line-height:1;white-space:nowrap}
.brand-tagline{position:absolute;left:119px;top:62px;font-size:10px;color:var(--blue);white-space:nowrap}
.main-nav a{position:absolute;top:43px;font-size:18px;color:#555;text-decoration:none;font-family:"Roboto",sans-serif}
.main-nav a.active{color:var(--blue)}
.nav-dot{position:absolute;left:474px;top:48px;width:12px;height:12px;background:var(--blue)}

/* hero */
.hero-photo{position:absolute;left:0;top:106px;width:1200px;height:573px;
  background:linear-gradient(110deg,#3e7f84 0%,#5d9ea1 35%,#8dbfc0 60%,#c9dfe0 85%,#e7efef 100%)}
.hero-title{position:absolute;left:80px;top:270px;font-family:"Ubuntu",sans-serif;font-weight:500;color:var(--white);line-height:1.05}
.hero-title .lg{font-size:62px;font-weight:700}
.hero-title .md{font-size:38px}
.hero-sub{position:absolute;left:80px;top:400px;font-size:23px;color:#e8f1f1}
.btn{position:absolute;display:flex;align-items:center;font-size:18px;text-transform:uppercase;text-decoration:none}
.btn-label{flex:1;height:100%;display:flex;align-items:center;justify-content:center}
.btn-icon{width:48px;height:100%;background:var(--black);display:flex;align-items:center;justify-content:center}
.btn-icon span{width:18px;height:18px;background:var(--blue)}
.btn-light .btn-label{background:var(--white);color:var(--ink)}
.btn-blue .btn-label{background:var(--blue);color:var(--white)}

/* about */
.about-photo{position:absolute;left:77px;top:729px;width:431px;height:283px;
  background:linear-gradient(135deg,#0b1a2e 0%,#1d3a5c 45%,#2f5b86 70%,#0f1f33 100%)}
.section-title{font-family:"Play",sans-serif;font-weight:400;color:var(--blue);font-size:40px;line-height:1}
.about-title{position:absolute;left:540px;top:728px}
.about-text{position:absolute;left:540px;top:790px;width:585px;font-size:14.5px;line-height:23px;color:var(--text)}

/* services */
.support-title{position:absolute;left:0;top:1062px;width:1200px;text-align:center}
.support-sub{position:absolute;left:250px;top:1120px;width:700px;text-align:center;font-size:14.5px;line-height:24px}
.service-card{position:absolute;top:1185px;width:204px;height:201px;border:1px solid #d7dadd;background:var(--white)}
.service-card.active{border:2px solid #d0d0d0;box-shadow:0 0 6px rgba(0,0,0,.18)}
.service-icon{position:absolute;left:49px;top:23px;width:106px;height:106px}
.service-name{position:absolute;left:0;top:155px;width:100%;text-align:center;font-size:16.5px;color:var(--ink)}
.service-card.active .service-name{color:var(--blue)}
.carousel-arrow{position:absolute;top:1270px;width:20px;height:28px}

/* strip */
.strip-tile{position:absolute;top:1436px;width:400px;height:262px}
.strip-caption{position:absolute;left:0;top:1558px;width:1200px;text-align:center;font-size:19px;color:var(--white)}

/* testimonial */
.testi-title{position:absolute;left:0;top:1750px;width:1200px;text-align:center;font-family:"Play",sans-serif;font-weight:400;font-size:40px;color:var(--blue)}
.testi-frame{position:absolute;left:150px;top:1810px}
.testi-quote{position:absolute;left:250px;top:1852px;width:700px;text-align:center;font-size:14.5px;line-height:23px}
.testi-name{position:absolute;left:0;top:1935px;width:1200px;text-align:center;font-family:"Play",sans-serif;font-size:22px;color:var(--blue)}
.testi-company{position:absolute;left:0;top:1964px;width:1200px;text-align:center;font-size:14px}

/* footer */
.site-footer{position:absolute;left:0;top:2073px;width:1200px;height:391px;
  background:linear-gradient(135deg,#f2f2f2 0%,#e9eaea 50%,#f0f0f0 100%)}
.footer-brand{position:absolute;left:77px;top:2150px;display:flex;align-items:center;gap:8px}
.footer-brand .brand-square{width:20px;height:20px}
.footer-brand .brand-name{font-size:19px;letter-spacing:.5px}
.footer-address{position:absolute;left:292px;top:2133px;font-size:14px;line-height:22px;color:#666;white-space:nowrap}
.footer-rule{position:absolute;left:77px;width:399px;height:1px;background:var(--line)}
.footer-divider{position:absolute;left:261px;top:2237px;width:1px;height:93px;background:var(--line)}
.contact-col{position:absolute;top:2243px;width:184px;text-align:center;font-size:14px}
.contact-col .lbl{margin-top:10px;color:var(--muted)}
.contact-col .val{margin-top:7px;color:var(--blue);font-size:15px}
.social{position:absolute;top:2361px;width:46px;height:46px;border:1.5px solid var(--blue)}
.social.filled{background:var(--blue)}
.touch-title{position:absolute;left:603px;top:2140px;font-family:"Play",sans-serif;font-weight:400;font-size:40px;color:var(--blue)}
.field{position:absolute;left:600px;width:255px;height:36px;border-bottom:1px solid #777;font-size:14px;color:var(--muted);padding:6px 0 0 8px}
.message{position:absolute;left:868px;top:2199px;width:255px;height:151px;border:1px solid #777;font-size:14px;color:var(--muted);padding:10px 12px}
.copyright{position:absolute;left:0;top:2464px;width:1200px;height:50px;background:var(--blue);color:var(--white);font-size:15px;display:flex;align-items:center;justify-content:center}
.copyright b{font-weight:500;margin:0 4px}
</style>
</head>
<body>

<header class="site-header">
  <div class="brand"><span class="brand-square"></span><span class="brand-name">KELVANBROOK</span></div>
  <div class="brand-tagline">Let us worry about your technology… So you don't have to!</div>
  <nav class="main-nav">
    <span class="nav-dot"></span>
    <a class="active" href="#" style="left:494px">Home</a>
    <a href="#" style="left:600px">About</a>
    <a href="#" style="left:706px">Support</a>
    <a href="#" style="left:821px">Clients</a>
    <a href="#" style="left:925px">Careers</a>
    <a href="#" style="left:1036px">Contact us</a>
  </nav>
</header>

<section>
  <div class="hero-photo" role="img" aria-label="Photo of a woman working on a laptop in a bright modern office"></div>
  <h1 class="hero-title"><span class="lg" style="font-size:54px">IT</span> <span class="md">solutions that</span> <span class="lg">WORK</span><br><span class="md">for</span> <span class="lg">YOUR</span> <span class="md">business.</span></h1>
  <p class="hero-sub">A full service technology company</p>
  <a class="btn btn-light" href="#" style="left:77px;top:449px;width:216px;height:54px"><span class="btn-label">Read More</span><span class="btn-icon"><span></span></span></a>
</section>

<section>
  <div class="about-photo" role="img" aria-label="Photo of a man working late at a desk with computer monitors"></div>
  <h2 class="section-title about-title">About Us</h2>
  <p class="about-text">Kelvanbrook Technology Group, Inc. was established in 1991. Our mission is helping businesses and individuals realize a Return on Investment by implementing today's advanced technologies. As a small business we understand the importance of technology and personalized attention.Every member of our support team has worked with both large and small companies supporting a multitude of applications, networks and environments.</p>
  <a class="btn btn-blue" href="#" style="left:536px;top:949px;width:216px;height:52px"><span class="btn-label">Read More</span><span class="btn-icon"><span></span></span></a>
</section>

<section>
  <h2 class="section-title support-title">IT Support Solution</h2>
  <p class="support-sub">Kelvanbrook is a technology solution provider based in Houston, Texas. Kelvanbrook has the experience, the tools, high-level technology solutions and training to power your business and your work force.</p>

  <svg class="carousel-arrow" style="left:28px" viewBox="0 0 20 28"><path d="M15 3 L5 14 L15 25" fill="none" stroke="#1b7bc3" stroke-width="3"/></svg>
  <svg class="carousel-arrow" style="left:1152px" viewBox="0 0 20 28"><path d="M5 3 L15 14 L5 25" fill="none" stroke="#1b7bc3" stroke-width="3"/></svg>

  <div class="service-card active" style="left:77px">
    <svg class="service-icon" viewBox="0 0 106 106"><circle cx="53" cy="53" r="50" fill="#fff" stroke="#222" stroke-width="3"/><circle cx="53" cy="53" r="44" fill="none" stroke="#ccc" stroke-width="2"/>
      <path d="M32 60 a9 9 0 0 1 4-17 a14 14 0 0 1 27-4 a11 11 0 0 1 11 21 z" fill="#1b7bc3"/>
      <rect x="44" y="48" width="4" height="10" fill="#fff"/><rect x="51" y="44" width="4" height="14" fill="#fff"/><rect x="58" y="50" width="4" height="8" fill="#fff"/></svg>
    <div class="service-name">Network Administration</div>
  </div>
  <div class="service-card" style="left:287px">
    <svg class="service-icon" viewBox="0 0 106 106"><circle cx="53" cy="53" r="50" fill="#fff" stroke="#1b7bc3" stroke-width="3"/><circle cx="53" cy="53" r="44" fill="none" stroke="#d8e6f1" stroke-width="2"/>
      <rect x="30" y="36" width="32" height="22" fill="none" stroke="#333" stroke-width="2.5"/><rect x="46" y="48" width="30" height="20" fill="#fff" stroke="#333" stroke-width="2.5"/><line x1="56" y1="73" x2="66" y2="73" stroke="#333" stroke-width="2.5"/></svg>
    <div class="service-name">Desktop Support</div>
  </div>
  <div class="service-card" style="left:497px">
    <svg class="service-icon" viewBox="0 0 106 106"><circle cx="53" cy="53" r="50" fill="#fff" stroke="#1b7bc3" stroke-width="3"/><circle cx="53" cy="53" r="44" fill="none" stroke="#d8e6f1" stroke-width="2"/>
      <path d="M30 66 q10-14 22-8 q12 6 22-10" fill="none" stroke="#333" stroke-width="2.5"/><rect x="60" y="36" width="16" height="12" fill="none" stroke="#333" stroke-width="2.5"/><line x1="64" y1="36" x2="64" y2="31" stroke="#333" stroke-width="2"/><line x1="70" y1="36" x2="70" y2="31" stroke="#333" stroke-width="2"/></svg>
    <div class="service-name">Network Cabling</div>
  </div>
  <div class="service-card" style="left:707px">
    <svg class="service-icon" viewBox="0 0 106 106"><circle cx="53" cy="53" r="50" fill="#fff" stroke="#1b7bc3" stroke-width="3"/><circle cx="53" cy="53" r="44" fill="none" stroke="#d8e6f1" stroke-width="2"/>
      <circle cx="53" cy="48" r="3.5" fill="#333"/><line x1="53" y1="52" x2="53" y2="70" stroke="#333" stroke-width="2.5"/>
      <path d="M44 40 a12 12 0 0 0 0 16 M62 40 a12 12 0 0 1 0 16 M38 34 a20 20 0 0 0 0 28 M68 34 a20 20 0 0 1 0 28" fill="none" stroke="#333" stroke-width="2.5"/></svg>
    <div class="service-name">Wireless Network</div>
  </div>
  <div class="service-card" style="left:917px">
    <svg class="service-icon" viewBox="0 0 106 106"><circle cx="53" cy="53" r="50" fill="#fff" stroke="#1b7bc3" stroke-width="3"/><circle cx="53" cy="53" r="44" fill="none" stroke="#d8e6f1" stroke-width="2"/>
      <g fill="#fff" stroke="#333" stroke-width="2.5"><line x1="42" y1="40" x2="64" y2="40"/><line x1="42" y1="40" x2="40" y2="64"/><line x1="64" y1="40" x2="66" y2="64"/><line x1="40" y1="64" x2="66" y2="64"/><line x1="53" y1="52" x2="42" y2="40"/><line x1="53" y1="52" x2="66" y2="64"/>
      <circle cx="42" cy="40" r="5"/><circle cx="64" cy="40" r="5"/><circle cx="40" cy="64" r="5"/><circle cx="66" cy="64" r="5"/><circle cx="53" cy="52" r="5"/></g></svg>
    <div class="service-name">Network Security</div>
  </div>
</section>

<section>
  <div class="strip-tile" style="left:0;background:linear-gradient(135deg,#5c6670,#9aa4ad 55%,#c8ccd0)" role="img" aria-label="Photo of a team gathered around a computer in a meeting"></div>
  <div class="strip-tile" style="left:400px;background:linear-gradient(135deg,#6b6e72,#8d9094 50%,#707378)" role="img" aria-label="Photo of two colleagues walking in an office corridor"></div>
  <div class="strip-tile" style="left:800px;background:linear-gradient(135deg,#d9dee3,#8c96a0 50%,#3a4048)" role="img" aria-label="Photo of network cables plugged into a switch"></div>
  <div class="strip-caption">Remote Diagnostic and Support</div>
</section>

<section>
  <h2 class="testi-title">TESTIMONIAL</h2>
  <svg class="testi-frame" width="900" height="215" viewBox="0 0 900 215">
    <polyline points="80,6 852,6 852,160" fill="none" stroke="#555" stroke-width="1.2"/>
    <polyline points="822,208 43,208 43,60" fill="none" stroke="#555" stroke-width="1.2"/>
    <g fill="#1b7bc3">
      <path d="M6 50 q0-30 24-44 l6 6 q-12 10-12 22 l12 0 l0 16 z"/>
      <path d="M40 50 q0-30 24-44 l6 6 q-12 10-12 22 l12 0 l0 16 z"/>
      <path d="M888 156 q0 30-24 44 l-6-6 q12-10 12-22 l-12 0 l0-16 z"/>
      <path d="M854 156 q0 30-24 44 l-6-6 q12-10 12-22 l-12 0 l0-16 z"/>
    </g>
  </svg>
  <p class="testi-quote">"Lorem Ipsum is simply dummy text of the printing and typesetting industry. Lorem Ipsum has been the industry's standard dummy text ever since the 1500s, when an unknown printer took a galley of type and scrambled it to make a type specimen book."</p>
  <div class="testi-name">- Dana Whitcombe</div>
  <div class="testi-company">Ridgeway Motors</div>
</section>

<footer>
  <div class="site-footer" role="img" aria-label="Faint street map background"></div>
  <div class="footer-brand"><span class="brand-square"></span><span class="brand-name">KELVANBROOK</span></div>
  <div class="footer-address">Kelvanbrook Technology Group, Inc.<br>1840 Marlow St.<br>Houston, Texas 77025</div>
  <div class="footer-rule" style="top:2226px"></div>
  <div class="footer-divider"></div>
  <div class="contact-col" style="left:77px">
    <svg width="18" height="18" viewBox="0 0 24 24"><path d="M6.6 10.8a15 15 0 0 0 6.6 6.6l2.2-2.2a1 1 0 0 1 1-.25 11.4 11.4 0 0 0 3.6.57 1 1 0 0 1 1 1V20a1 1 0 0 1-1 1A17 17 0 0 1 3 4a1 1 0 0 1 1-1h3.5a1 1 0 0 1 1 1c0 1.25.2 2.45.57 3.57a1 1 0 0 1-.25 1z" fill="#1b7bc3"/></svg>
    <div class="lbl">Call us</div>
    <div class="val">(713) 555-0148</div>
  </div>
  <div class="contact-col" style="left:282px">
    <svg width="18" height="18" viewBox="0 0 24 24"><rect x="2" y="5" width="20" height="14" fill="#1b7bc3"/><path d="M2 5 L12 13 L22 5" fill="none" stroke="#fff" stroke-width="2"/></svg>
    <div class="lbl">Email or Our Address</div>
    <div class="val">info@kelvanbrook.com</div>
  </div>
  <div class="footer-rule" style="top:2351px"></div>
  <a class="social filled" href="#" aria-label="Social profile one" style="left:178px"></a>
  <a class="social" href="#" aria-label="Social profile two" style="left:234px"></a>
  <a class="social" href="#" aria-label="Social profile three" style="left:290px"></a>

  <h2 class="touch-title">GET IN TOUCH</h2>
  <div class="field" style="top:2196px">Name</div>
  <div class="field" style="top:2255px">Email Id</div>
  <div class="field" style="top:2314px">Contact No</div>
  <div class="message">Message...</div>
  <a class="btn btn-blue" href="#" style="left:600px;top:2358px;width:215px;height:52px"><span class="btn-label">Submit</span><span class="btn-icon"><span></span></span></a>

  <div class="copyright">© <b>Kelvanbrook Technology Group,Inc.</b> - 2017 All Right Reserved</div>
</footer>

</body>
</html>
```